Harborview Optical -Window Poster (Optometrist)

We are an optometry practice and we need a poster for a new store promotion for our window highlighting we now also sell 2 pairs of glasses as a package deal. The size will be 1300mm width x 1900mm height

The artwork will be displayed as a fabric banner in our shop window. We have 7 other banners with different services our business provides. The words needs to standout for passers by and the cars stopped at the traffic lights out front of our business. We already have signs with our logos phone number etc. so we won't need them included in the poster.

It would need to include the following information.

Two pair packages now available*

*Conditions apply

The artwork will be displayed as a fabric banner in our shop window. We have 7 other banners with different services our business provides. The words needs to standout for passers by and the cars stopped at the traffic lights out front of our business. We already have signs with our logos phone number etc. so we won't need them included in the poster. Thank you for your work it's amazing Added Saturday, February 18, 2017

The artwork will be displayed as a fabric banner in our shop window. We have 7 other banners with different services our business provides. The words needs to standout for passers by and the cars stopped at the traffic lights out front of our business. We already have signs with our logos phone number etc. so we won't need them included in the poster. Added Saturday, February 18, 2017

Target Market(s)

Cars driving past and stopped at traffic lights outside our store.

Industry/Entity Type

Optician

Requirements
Must have
• Poster must say:
• Two pair packages now available*
• *Conditions apply

```html
<!DOCTYPE html>
<html lang="en">
<head>
<meta charset="utf-8">
<title>Harborview Optical – Two Pair Packages Window Poster</title>
<link rel="stylesheet" href="https://fonts.googleapis.com/css2?family=Archivo+Black&family=Bebas+Neue&family=Alegreya+Sans+SC:wght@800&display=swap">
<style>
  :root {
    --page-bg: #eeeeee;
    --amber-light: #c8872f;
    --amber-dark: #a2622b;
    --panel-gold: #ebbf22;
    --panel-glow: #ffe400;
    --headline-white: #ffffff;
    --headline-red: #e8202a;
    --shadow-black: #141010;
    --ink: #111111;
  }
  html, body {
    margin: 0;
    padding: 0;
    width: 962px;
    height: 1200px;
    overflow: hidden;
    background: var(--page-bg);
  }
  .poster {
    position: absolute;
    left: 70px;
    top: 0;
    width: 821px;
    height: 1200px;
    overflow: hidden;
  }
  .poster__backdrop {
    position: absolute;
    inset: 0;
    background:
      radial-gradient(ellipse 300px 200px at 560px 860px, rgba(235,170,60,0.55), rgba(235,170,60,0) 70%),
      radial-gradient(ellipse 520px 520px at 430px 370px, var(--amber-light), rgba(200,135,47,0) 80%),
      linear-gradient(135deg, var(--amber-dark) 0%, var(--amber-light) 45%, var(--amber-dark) 100%);
  }
  .poster__fade {
    position: absolute;
    inset: 0;
    background: linear-gradient(to bottom,
      rgba(0,0,0,0) 0px,
      rgba(0,0,0,0) 900px,
      rgba(90,50,20,0.75) 1000px,
      rgba(40,5,5,0.95) 1090px,
      #000 1150px);
  }
  .poster__art {
    position: absolute;
    inset: 0;
  }
  .kicker {
    font-family: "Bebas Neue", "Oswald", sans-serif;
    fill: var(--ink);
  }
  .headline-top {
    font-family: "Archivo Black", "Arial Black", sans-serif;
    fill: var(--headline-white);
  }
  .headline-bottom {
    font-family: "Archivo Black", "Arial Black", sans-serif;
    fill: var(--headline-red);
  }
  .headline-bottom--shadow {
    fill: var(--shadow-black);
  }
  .disclaimer {
    font-family: "Alegreya Sans SC", "Copperplate", sans-serif;
    font-weight: 800;
    fill: var(--headline-white);
  }
</style>
</head>
<body>
<main class="poster">
  <div class="poster__backdrop" role="img" aria-label="Amber sunburst rays radiating from behind the headline"></div>
  <div class="poster__fade"></div>
  <svg class="poster__art" width="821" height="1200" viewBox="0 0 821 1200" xmlns="http://www.w3.org/2000/svg">
    <defs>
      <radialGradient id="panelGlowTop" cx="428" cy="360" r="240" gradientUnits="userSpaceOnUse">
        <stop offset="0" stop-color="#ffe400"/>
        <stop offset="1" stop-color="#ebbf22" stop-opacity="0"/>
      </radialGradient>
      <radialGradient id="panelGlowLeft" cx="225" cy="702" r="180" gradientUnits="userSpaceOnUse">
        <stop offset="0" stop-color="#ffe400"/>
        <stop offset="1" stop-color="#ebbf22" stop-opacity="0"/>
      </radialGradient>
      <radialGradient id="panelGlowRight" cx="631" cy="778" r="160" gradientUnits="userSpaceOnUse">
        <stop offset="0" stop-color="#ffe400" stop-opacity="0.8"/>
        <stop offset="1" stop-color="#ebbf22" stop-opacity="0"/>
      </radialGradient>
      <radialGradient id="letterGlow" cx="206" cy="645" r="80" gradientUnits="userSpaceOnUse">
        <stop offset="0" stop-color="#ff7a22"/>
        <stop offset="1" stop-color="#e8202a"/>
      </radialGradient>
    </defs>

    <text class="kicker" x="441" y="251" font-size="74" text-anchor="middle" textLength="396" lengthAdjust="spacingAndGlyphs">NOW AVAILABLE*</text>

    <polygon class="panel-frame" points="49,316 727,264 784,785 104,838" fill="none" stroke="#ffffff" stroke-width="2.5"/>

    <g class="panel">
      <rect x="75" y="288" width="683" height="526" fill="#ebbf22"/>
      <rect x="75" y="288" width="683" height="526" fill="url(#panelGlowTop)"/>
      <rect x="75" y="288" width="683" height="526" fill="url(#panelGlowLeft)"/>
      <rect x="75" y="288" width="683" height="526" fill="url(#panelGlowRight)"/>
    </g>

    <text class="headline-top" x="102" y="509" font-size="156" textLength="627" lengthAdjust="spacingAndGlyphs">TWO PAIR</text>

    <text class="headline-bottom headline-bottom--shadow" x="109" y="688" font-size="178" textLength="643" lengthAdjust="spacingAndGlyphs">PACKAGES</text>
    <text class="headline-bottom" x="104" y="683" font-size="178" textLength="643" lengthAdjust="spacingAndGlyphs" fill="url(#letterGlow)">PACKAGES</text>

    <text class="disclaimer" x="151" y="1100" font-size="60" textLength="552" lengthAdjust="spacingAndGlyphs">*Conditions apply</text>
  </svg>
</main>
</body>
</html>
```